Croatia Luxury Cruise Brochure

1) Front page instead of By Journeys of Perla please put by Sea Lantern Voyages – same on the last page where you have her contacts
2) Can you please add into the second page where you have ‘Welcome to your Croatia trip’ itinerary at glance. You can put it just below the text you have. Create a nice looking table .
D1 August 05, 2023 Arrival to Dubrovnik , Welcome cocktail party on Dubrovnik city walls
D2 August 06, 2023 Dubrovnik Highlights city tour – Embark sail to Elafiti
D3 August 07, 2023 Sail to Mljet island and day at leisure at sea
D4 August 08, 2023 Peljesac Wine Tasting with Live Music – Sail to Korcula
D5 August 09, 2023 Korcula Highlights Explorer Tour & Local Estate Dinner
D6 August 10, 2023 Korcula to Vis Island sail
D7 August 11, 2023 Vis Militarty Tour -sail to Pakleni Islands Vetrovo sunset cocktails
D8 August 12, 2023 Hvar island – sail to Split
D9 August 13, 2023 Disembark – Split & Trogir ORTHAV tours with 6-course wine dinner
D10 August 14, 2023 Fly out
Note: All tours & Experiences are optional add ons except the Cocktail reception on Dubrovnik city walls
3) Changes to the itinerary:
D1 is now arrival to Dubrovnik day earlier (AUGU5) and the rest is all moved accordingly. Please check the link
https://portal.bluekeelroutes. com/itinerary/custom-trip-prepared-for-perla-group/
4) Inclusion/Exclusion page we need to update a little. Please make 3 different categories with a note for booking conditions.
Inclusions
• All transfers per itinerary including airport pick up and drop off
• 7 nights cruise on MS Gullwing on half board basis
• All meals stated per itinerary
• Captains dinner
• Unlimited water
• Masseuse on board
• Service of 11 crew members
• Cruise director
• Unlimited WiFi
• Daily cleaning
• Arrival refreshments
• Premium docking
• Usage of non motorized water toys
• Exclusive cocktail reception on Dubrovnik city walls with live music and snacks
Optional Tours
• Dubrovnik Highlights Explorer tour
• Peljesac Wine tour with live music
• Korcula explorer tour with local estate dinner
• Vis Military tour
• Vetrovo Lounge bar reservation (min spend EUR100 per person)
• Split & Trogir ORTHAV Explorer tour
• 6-course farewell dinner with local wine pairing
• 1 night post stay in Belvani 5* hotel in Split (This is added on optional)
Extras
• Tips for the crew
• Beverage consumption
• Usage of motorized water toys – EUR150 per hour
• International flights
• Any personal expenses
Booking conditions
30 % non-refundable deposit needed upon confirmation
Balance of the trip and any optional tours picked are due 06 May, 2023
Luxury travelers from USA and Canada
Tourism

```html
<!DOCTYPE html>
<html lang="en">
<head>
<meta charset="utf-8">
<title>Croatia Cruise Brochure – Day 2 Spread</title>
<link rel="stylesheet" href="https://fonts.googleapis.com/css2?family=Libre+Baskerville:wght@400;700&family=Montserrat:wght@400;600;700&display=swap">
<style>
  :root {
    --backdrop: #cbcbcb;
    --paper: #f7f7f7;
    --red: #e0252b;
    --ribbon: #e8444f;
    --ink: #2a2a2a;
    --body-ink: #3a3a3a;
    --sky-top: #1f86e0;
    --sky-mid: #64b6ef;
    --haze: #dfe8f1;
    --stone-light: #cdbda6;
    --stone-dark: #6f6254;
  }
  * { box-sizing: border-box; margin: 0; padding: 0; }
  html, body {
    width: 1200px; height: 900px; overflow: hidden;
    background: var(--backdrop);
  }
  .spread {
    position: absolute; left: 40px; top: 54px;
    width: 1120px; height: 792px;
    display: flex;
    box-shadow: 0 10px 30px rgba(0,0,0,.18);
  }
  .page { position: relative; width: 560px; height: 792px; overflow: hidden; background: var(--paper); }
  .street-photo {
    position: absolute; top: 0; height: 100%;
    background: linear-gradient(180deg, var(--sky-top) 0%, var(--sky-mid) 28%, var(--haze) 52%, var(--stone-light) 68%, var(--stone-dark) 100%);
  }
  .page--left .street-photo { left: 0; width: 100%; }
  .page--right .street-photo { left: 0; width: 100px; }
  .spine-shade {
    position: absolute; top: 0; bottom: 0; width: 40px; pointer-events: none;
  }
  .page--left .spine-shade { right: 0; background: linear-gradient(90deg, rgba(0,0,0,0), rgba(0,0,0,.12)); }
  .page--right .spine-shade { left: 0; background: linear-gradient(90deg, rgba(0,0,0,.12), rgba(0,0,0,0)); }

  .info-band { position: absolute; inset: 0; }
  .location {
    position: absolute; left: 46px; top: 676px;
    display: flex; align-items: center; gap: 14px; color: #fff;
    font-family: "Montserrat", sans-serif;
  }
  .location__name { font-weight: 700; font-size: 17px; line-height: 1; }
  .location__sub { font-size: 6.5px; letter-spacing: .6px; margin-top: 3px; }
  .facts {
    position: absolute; left: 26px; right: 20px; top: 742px;
    display: flex; gap: 22px;
    font-family: "Montserrat", sans-serif;
  }
  .fact { display: flex; align-items: center; gap: 10px; flex: 1; }
  .fact__label { color: var(--red); font-size: 7px; }
  .fact__value { color: var(--ink); font-weight: 700; font-size: 10.5px; line-height: 1.15; }

  .day-ribbon {
    position: absolute; left: 210px; top: 0; width: 112px; height: 158px;
  }
  .day-ribbon__text {
    position: absolute; left: 0; right: 0; top: 30px; text-align: center; color: #fff;
  }
  .day-ribbon__label { font-family: "Montserrat", sans-serif; font-size: 11px; font-weight: 600; letter-spacing: .5px; }
  .day-ribbon__number { font-family: "Libre Baskerville", serif; font-size: 38px; line-height: 1.1; }

  .day-title {
    position: absolute; left: 150px; top: 218px; width: 330px;
    font-family: "Libre Baskerville", serif; font-weight: 700;
    font-size: 20px; line-height: 1.3; color: var(--ink);
  }
  .day-body {
    position: absolute; left: 160px; top: 318px; width: 350px;
    font-family: "Montserrat", sans-serif; font-size: 10.5px; line-height: 1.75;
    color: var(--body-ink);
  }
</style>
</head>
<body>
<main class="spread">
  <section class="page page--left">
    <div class="street-photo" role="img" aria-label="Photo of Dubrovnik's main stone street at dawn with a bell tower under a blue sky"></div>
    <svg class="info-band" viewBox="0 0 560 792" aria-hidden="true">
      <path d="M0 716 C0 684 24 668 70 666 L560 656 L560 726 L0 744 Z" fill="var(--red)"/>
      <path d="M0 744 L560 726 L560 792 L0 792 Z" fill="#fff"/>
    </svg>
    <div class="location">
      <svg width="16" height="20" viewBox="0 0 16 20" aria-hidden="true">
        <path d="M8 0C3.6 0 0 3.5 0 7.8 0 13.5 8 20 8 20s8-6.5 8-12.2C16 3.5 12.4 0 8 0z" fill="#fff"/>
        <circle cx="8" cy="7.8" r="3" fill="var(--red)"/>
      </svg>
      <div>
        <div class="location__name">Dubrovnik City</div>
        <div class="location__sub">DUBROVNIK WALKING TOUR</div>
      </div>
    </div>
    <div class="facts">
      <div class="fact">
        <svg width="26" height="24" viewBox="0 0 26 24" fill="none" stroke="var(--red)" stroke-width="1.4" aria-hidden="true">
          <rect x="1" y="4" width="24" height="19" rx="2"/><line x1="1" y1="10" x2="25" y2="10"/>
          <line x1="7" y1="1" x2="7" y2="6"/><line x1="19" y1="1" x2="19" y2="6"/>
        </svg>
        <div><div class="fact__label">Date</div><div class="fact__value">9 October<br>2023</div></div>
      </div>
      <div class="fact">
        <svg width="30" height="20" viewBox="0 0 30 20" fill="none" stroke="var(--red)" stroke-width="1.4" aria-hidden="true">
          <line x1="1" y1="2" x2="1" y2="19"/><line x1="29" y1="9" x2="29" y2="19"/>
          <path d="M1 15 H29"/><path d="M10 9 H27 a2 2 0 0 1 2 2 V15 H10 Z"/><circle cx="5.5" cy="11.5" r="2.5"/>
        </svg>
        <div><div class="fact__label">Accomodation</div><div class="fact__value">Mini Cruiser<br>Gullwing</div></div>
      </div>
      <div class="fact">
        <svg width="32" height="22" viewBox="0 0 32 22" fill="none" stroke="var(--red)" stroke-width="1.4" aria-hidden="true">
          <circle cx="16" cy="11" r="9"/><circle cx="16" cy="11" r="5.5"/>
          <line x1="2" y1="2" x2="2" y2="20"/><path d="M0.5 2 V7 a1.5 1.5 0 0 0 3 0 V2"/>
          <path d="M30 2 C27 4 27 10 30 11 V20"/>
        </svg>
        <div><div class="fact__label">Meals</div><div class="fact__value">Breakfast and Dinner<br>on board, Snack</div></div>
      </div>
    </div>
    <div class="spine-shade"></div>
  </section>

  <section class="page page--right">
    <div class="street-photo" role="img" aria-label="Continuation of the Dubrovnik street photo with stone facades"></div>
    <svg class="day-ribbon" viewBox="0 0 112 158" aria-hidden="true">
      <path d="M0 0 H112 V128 L56 158 L0 128 Z" fill="var(--ribbon)"/>
    </svg>
    <div class="day-ribbon" aria-label="Day 2">
      <div class="day-ribbon__text">
        <div class="day-ribbon__label">DAY</div>
        <div class="day-ribbon__number">2</div>
      </div>
    </div>
    <h1 class="day-title">Dubrovnik City Explorer Tour and Wine Event with Live Local Music</h1>
    <p class="day-body">After breakfast it is the time to Explore the wonders of Dubrovnik's old town, a ORTHAV World Heritage Site and one of the most important living historical monuments in this part of Europe. Your local guide will show you this magical medieval town full of legends and give you a glimpse into the incredible history that makes Dubrovnik such a unique city. Explore Dubrovnik's famed City Walls and enjoy a unique view of the Old Town from above, including its narrow streets and small squares. Today Dubrovnik is one of the most beautiful towns in the Mediterranean and you will see why. Dubrovnik used to be an independent republic, surviving mostly on trade. The whole city is alive with tourists and locals who wander the centuries-old streets admiring the architecture. After the city tour, we will have a private wine event in one of the wine cellars within the old town of Dubrovnik. Enjoy local wines accompanied with with live music. After the private event, free time in Dubrovnik to enjoy the city on your own before another dinner on board prepared by our chef on board of Gullwing.</p>
    <div class="spine-shade"></div>
  </section>
</main>
</body>
</html>
```